Automotive eCommerce Business looking for a business card design

Looking for a clean and simple business card design. Our company name is "Brindle Auto" and we are a company specializing in the ecommerce sales of automotive parts, specifically for pick up trucks and large SUVs. Our company colours are red, black, and white.

Feel free to use the logo provided or create a new logo that you seem fit. Looking forward to your creative ideas!

Industry/Entity Type

Automotive

Contact Information for Business Card

We were thinking of a possibly two-sided design featuring just the logo and company name on one side, and personal information on the other side. Single sided designs will be considered as well.

Font styles to use
Serif
Sans Serif
Decorative

Colors
ec1f27
ffffff
000000

Requirements
Must have
• Space for employee's name, title, phone number and email address, along with the company address and website somewhere.

```html
<!DOCTYPE html>
<html lang="en">
<head>
<meta charset="utf-8">
<title>Brindle Auto Ltd. — Business Card</title>
<link href="https://fonts.googleapis.com/css2?family=Libre+Baskerville&family=Oswald:wght@500&family=Roboto+Condensed:wght@400&display=swap" rel="stylesheet">
<style>
  :root {
    --backdrop: #2a2a2a;
    --brand-red: #9e1c22;
    --card-white: #f4f4f3;
    --ink-grey: #4a4a4a;
    --ink-dark: #333333;
    --white: #ffffff;
  }
  * { box-sizing: border-box; margin: 0; padding: 0; }
  html, body { width: 1200px; height: 886px; overflow: hidden; }
  body {
    background: var(--backdrop);
    position: relative;
    font-family: "Roboto Condensed", sans-serif;
  }

  /* Brand side */
  .card-brand {
    position: absolute;
    left: 70px; top: 283px;
    width: 560px; height: 320px;
    background: var(--brand-red);
    border-radius: 20px;
    display: flex; flex-direction: column;
    align-items: center; justify-content: center;
  }
  .card-brand .wordmark {
    font-family: "Libre Baskerville", serif;
    color: var(--white);
    font-size: 30px;
    letter-spacing: 2px;
    text-transform: uppercase;
  }
  .card-brand .web-address {
    position: absolute;
    bottom: 34px; left: 0; right: 0;
    text-align: center;
    color: var(--white);
    font-family: "Roboto Condensed", sans-serif;
    font-size: 13px;
    letter-spacing: 6px;
  }

  /* Contact side */
  .card-contact {
    position: absolute;
    left: 770px; top: 146px;
    width: 340px; height: 594px;
    background: var(--card-white);
    border-radius: 20px;
    display: flex; flex-direction: column; align-items: center;
    padding-top: 52px;
    text-align: center;
  }
  .brand-lockup { display: flex; flex-direction: column; align-items: center; gap: 22px; }
  .brand-square { width: 64px; height: 64px; background: var(--brand-red); }
  .brand-name {
    font-family: "Libre Baskerville", serif;
    color: var(--ink-grey);
    font-size: 20px;
    letter-spacing: 1px;
    text-transform: uppercase;
  }
  .person-name {
    margin-top: 46px;
    font-family: "Oswald", sans-serif;
    font-weight: 500;
    color: var(--brand-red);
    font-size: 30px;
    letter-spacing: 0.5px;
    line-height: 1;
  }
  .person-title {
    margin-top: 6px;
    color: var(--ink-dark);
    font-size: 17px;
    letter-spacing: 0.5px;
  }
  .divider {
    width: 20px; height: 2px;
    background: var(--brand-red);
    margin: 18px 0;
  }
  .address { color: var(--ink-dark); font-size: 16px; line-height: 1.35; }
  .contact-list { list-style: none; color: var(--ink-dark); font-size: 16px; line-height: 1.4; }
  .contact-list li { display: flex; align-items: center; justify-content: center; gap: 6px; }
  .contact-list svg { width: 13px; height: 13px; fill: var(--brand-red); flex: none; }
</style>
</head>
<body>

  <section class="card-brand" aria-label="Card brand side">
    <p class="wordmark">Brindle Auto Ltd.</p>
    <p class="web-address">www.brindleauto.net</p>
  </section>

  <section class="card-contact" aria-label="Card contact side">
    <div class="brand-lockup">
      <div class="brand-square"></div>
      <p class="brand-name">Brindle Auto Ltd.</p>
    </div>

    <h1 class="person-name">AARON PELL</h1>
    <p class="person-title">CEO/FOUNDER</p>
    <div class="divider"></div>
    <p class="address">412 Harlow Street<br>Juneau, Alaska 99801</p>
    <div class="divider"></div>

    <ul class="contact-list">
      <li>
        <svg viewBox="0 0 16 16"><path d="M3.5 1l2.5 3-1.5 1.5c.8 2 2.5 3.7 4.5 4.5L10.5 8.5l3 2.5-1.5 3C7 14 2 9 2 2.5z"/></svg>
        907 555 0142
      </li>
      <li>
        <svg viewBox="0 0 16 16"><path d="M4 1h8v14H4zM5.5 2.5v9h5v-9z"/></svg>
        907 555 0187
      </li>
      <li>
        <svg viewBox="0 0 16 16"><path d="M4 2h7v4H4zM2 7h12v7H2zM4 9v1h3V9z"/></svg>
        907 555 0163
      </li>
      <li>
        <svg viewBox="0 0 16 16"><path d="M1 3h14v10H1zM2.5 4.5l5.5 4 5.5-4z"/></svg>
        aaron@brindleauto.net
      </li>
      <li>
        <svg viewBox="0 0 16 16"><circle cx="8" cy="8" r="7"/></svg>
        www.brindleauto.net
      </li>
    </ul>
  </section>

</body>
</html>
```